New Business Card Design Project

Need a design that will create an impact / strong impression towards our clients for our business. We are in the lighting business and we do lighting retrofits for large commercial to industrial clientele.

Target Market(s)

Lighting Industry

Industry/Entity Type

Business

Font styles to use
Other font styles liked:
• we would like to use the font on our logo, not sure what it is though..

Requirements
Must have
• Our logo.
Nice to have
• We are open to suggestions that have to do with lighting.

```html
<!DOCTYPE html>
<html lang="en">
<head>
<meta charset="utf-8">
<title>Kelvara Retrofit Group – Business Card</title>
<link rel="stylesheet" href="https://fonts.googleapis.com/css2?family=Montserrat:wght@400;500;600;700&display=swap">
<style>
  :root {
    --backdrop: #262626;
    --paper: #ffffff;
    --green-deep: #173f14;
    --green-mid: #0b8136;
    --green-bright: #6cc85a;
    --ink-grey: #555555;
    --white: #ffffff;
  }
  * { margin: 0; padding: 0; box-sizing: border-box; }
  html, body {
    width: 1200px; height: 960px; overflow: hidden;
    background: var(--backdrop);
    font-family: "Montserrat", sans-serif;
  }
  .canvas { position: relative; width: 1200px; height: 960px; }

  .card { position: absolute; width: 600px; height: 343px; }
  .card-front { left: 314px; top: 113px; background: var(--paper); }
  .card-back { left: 311px; top: 472px; background: var(--green-mid); }

  .wordmark {
    position: absolute; font-weight: 700; line-height: 1; white-space: nowrap;
  }
  .card-front .wordmark { left: 25px; top: 32px; font-size: 48px; color: var(--green-deep); letter-spacing: 0.5px; }
  .wordmark-rule { position: absolute; height: 2px; }
  .card-front .wordmark-rule { left: 26px; top: 89px; width: 234px; background: var(--green-deep); }
  .legal-name {
    position: absolute; font-weight: 500; letter-spacing: 0.6px;
    text-transform: uppercase; white-space: nowrap;
  }
  .card-front .legal-name { left: 26px; top: 95px; font-size: 9.5px; color: var(--green-deep); }

  .person-name { position: absolute; left: 26px; top: 121px; font-weight: 700; font-size: 19px; color: var(--green-deep); letter-spacing: 0.5px; }
  .person-role { position: absolute; left: 26px; top: 145px; font-weight: 400; font-size: 16px; color: var(--green-mid); }
  .address { position: absolute; left: 25px; top: 169px; font-size: 15.5px; line-height: 19px; color: var(--ink-grey); }

  .contact-list { position: absolute; left: 25px; top: 213px; list-style: none; }
  .contact-list li { display: flex; align-items: center; height: 19px; font-size: 15.5px; color: var(--ink-grey); }
  .contact-list svg { width: 13px; height: 13px; margin-right: 9px; fill: var(--green-deep); }

  .step-decoration {
    position: absolute; left: 366px; top: 158px; width: 228px; height: 140px;
    background: linear-gradient(90deg, var(--green-bright), var(--green-mid) 50%, var(--green-deep));
  }
  .footer-rule { position: absolute; left: 0; top: 297px; width: 594px; height: 2px; background: var(--green-mid); }
  .website { position: absolute; left: 22px; top: 311px; font-size: 11.5px; font-weight: 700; letter-spacing: 0.8px; color: var(--ink-grey); text-transform: uppercase; white-space: nowrap; }

  .card-back .wordmark { left: 141px; top: 126px; font-size: 58px; color: var(--white); letter-spacing: 1px; }
  .card-back .wordmark-rule { left: 142px; top: 192px; width: 318px; background: var(--white); }
  .card-back .legal-name { left: 142px; top: 201px; font-size: 11.5px; color: var(--white); }
</style>
</head>
<body>
<main class="canvas">
  <section class="card card-front" aria-label="Card front">
    <div class="wordmark">KELVARA</div>
    <div class="wordmark-rule"></div>
    <div class="legal-name">Kelvara Retrofit Group, LLC.</div>

    <div class="person-name">DANA WHITFIELD</div>
    <div class="person-role">CEO/FOUNDER</div>
    <div class="address">2140 Harbor View Road<br>Fairbanks, Alaska 99701</div>

    <ul class="contact-list">
      <li><svg viewBox="0 0 16 16"><path d="M2 5c0-2 3-3 6-3s6 1 6 3v1h-3V5H5v1H2zM3 7h10l1 7H2z"/></svg>555 210 4471</li>
      <li><svg viewBox="0 0 16 16"><path d="M4 0h8v16H4zM5.5 2v10h5V2z"/></svg>555 318 2096</li>
      <li><svg viewBox="0 0 16 16"><path d="M4 1h8v4H4zM1 6h14v6h-3v3H4v-3H1zM5 10v4h6v-4z"/></svg>555 742 6153</li>
      <li><svg viewBox="0 0 16 16"><path d="M1 4h14v1L8 9 1 5zM1 7l7 4 7-4v6H1z"/></svg>info@kelvara.example</li>
    </ul>

    <div class="step-decoration" role="img" aria-label="Rising stepped green bar decoration"></div>
    <div class="footer-rule"></div>
    <div class="website">www.kelvararetrofitgroup.example</div>
  </section>

  <section class="card card-back" aria-label="Card back">
    <div class="wordmark">KELVARA</div>
    <div class="wordmark-rule"></div>
    <div class="legal-name">Kelvara Retrofit Group, LLC.</div>
  </section>
</main>
</body>
</html>
```